SaaS Early tech startup business card design

Unique design for experience ecommerce platform company. the business cards will be used by executive members. conformance with color code is required.

```html
<!DOCTYPE html>
<html lang="en">
<head>
<meta charset="utf-8">
<title>nuvio — business card</title>
<link rel="stylesheet" href="https://fonts.googleapis.com/css2?family=Montserrat:wght@400;500;700&display=swap">
<style>
  :root {
    --page: #e9eaee;
    --card: #27273f;
    --card-shadow: rgba(20, 20, 40, 0.25);
    --teal: #2fc3a0;
    --teal-soft: #4fd6b4;
    --blue: #1b6e9e;
    --ink-light: #ffffff;
    --ornament-a: #1d6e98;
    --ornament-b: #3cc8a8;
  }
  * { box-sizing: border-box; margin: 0; padding: 0; }
  html, body {
    width: 1200px; height: 900px; overflow: hidden;
    background: var(--page);
    font-family: "Montserrat", Arial, sans-serif;
    color: var(--ink-light);
  }
  .canvas {
    position: relative; width: 1200px; height: 900px;
  }
  .card {
    position: absolute; left: 250px;
    width: 700px; height: 400px;
    background: var(--card);
    border-radius: 22px;
    overflow: hidden;
    box-shadow: 0 14px 30px var(--card-shadow);
  }
  .card--front { top: 35px; }
  .card--back { top: 465px; }
  .card__band {
    position: absolute; left: 0; right: 0; bottom: 0; height: 18px;
    background: linear-gradient(90deg, var(--blue) 0%, #1f8fb0 45%, var(--teal) 70%, var(--teal-soft) 100%);
  }
  .brand-name {
    position: absolute;
    font-weight: 700;
    color: var(--teal);
    letter-spacing: -2px;
    line-height: 1;
  }
  .card--front .brand-name { right: 60px; top: 40px; font-size: 92px; }
  .card--back .brand-name { left: 250px; top: 70px; font-size: 120px; }

  .ornament {
    position: absolute; right: 30px; top: 165px;
    width: 200px; height: 150px;
    border-radius: 40px;
    background: radial-gradient(ellipse at center, rgba(60,200,168,0.35), rgba(29,110,152,0.12) 70%, transparent 100%);
  }
  .stat {
    position: absolute; left: 55px; top: 170px;
  }
  .stat__value {
    font-size: 72px; font-weight: 500; color: var(--teal); line-height: 1;
  }
  .stat__text {
    margin-top: 10px;
    font-size: 26px; font-weight: 500; line-height: 1.3;
  }

  .person {
    position: absolute; right: 390px; top: 240px; text-align: right;
  }
  .person__name { font-size: 32px; font-weight: 700; color: var(--teal); }
  .person__role { font-size: 22px; font-weight: 500; margin-top: 2px; }
  .divider {
    position: absolute; left: 330px; top: 225px;
    width: 2px; height: 90px; background: var(--ink-light);
  }
  .contacts {
    position: absolute; left: 355px; top: 225px;
    list-style: none;
  }
  .contacts li {
    display: flex; align-items: center; gap: 12px;
    font-size: 22px; font-weight: 500; height: 30px;
  }
  .contact-icon {
    width: 24px; height: 24px; flex: none;
    background: var(--teal); border-radius: 6px;
    display: flex; align-items: center; justify-content: center;
  }
  .address {
    position: absolute; left: 230px; top: 335px;
    font-size: 22px; font-weight: 500;
  }
</style>
</head>
<body>
<main class="canvas">

  <section class="card card--front">
    <div class="brand-name">nuvio</div>
    <div class="ornament" role="img" aria-label="Decorative flowing line-art knot in blue and teal"></div>
    <div class="stat">
      <div class="stat__value">63%</div>
      <p class="stat__text">Of Consumer Value<br>Privacy Over Popularity<br>When Dealing With<br>Online Platfrom</p>
    </div>
    <div class="card__band"></div>
  </section>

  <section class="card card--back">
    <div class="brand-name">nuvio</div>

    <div class="person">
      <div class="person__name">Daniel Reyes</div>
      <div class="person__role">Manager</div>
    </div>
    <div class="divider"></div>

    <ul class="contacts">
      <li>
        <span class="contact-icon">
          <svg width="14" height="14" viewBox="0 0 24 24"><path fill="#27273f" d="M6.6 10.8a15 15 0 0 0 6.6 6.6l2.2-2.2c.3-.3.7-.4 1-.2 1.1.4 2.3.6 3.6.6.6 0 1 .4 1 1V20c0 .6-.4 1-1 1A17 17 0 0 1 3 4c0-.6.4-1 1-1h3.5c.6 0 1 .4 1 1 0 1.3.2 2.5.6 3.6.1.3 0 .7-.2 1z"/></svg>
        </span>
        123-555-0190
      </li>
      <li>
        <span class="contact-icon">
          <svg width="14" height="14" viewBox="0 0 24 24" fill="none" stroke="#27273f" stroke-width="2.5"><rect x="3" y="5" width="18" height="14" rx="1"/><path d="M3 6l9 7 9-7"/></svg>
        </span>
        hello@nuviomail.com
      </li>
      <li>
        <span class="contact-icon">
          <svg width="14" height="14" viewBox="0 0 24 24" fill="none" stroke="#27273f" stroke-width="2.2"><circle cx="12" cy="12" r="9"/><path d="M3 12h18M12 3c3 3 3 15 0 18M12 3c-3 3-3 15 0 18"/></svg>
        </span>
        www.nuvioplatform.com
      </li>
    </ul>

    <p class="address">Your address, city, state, ZIP 0000</p>
    <div class="card__band"></div>
  </section>

</main>
</body>
</html>
```